Frostvale Harborline LLC

we need a business card design

Industry/Entity Type

hvac

Contact Information for Business Card

my logo

Requirements
Must have
• my logo and same colors

```html
<!DOCTYPE html>
<html lang="en">
<head>
<meta charset="utf-8">
<title>Frostvale Harborline LLC – Business Card</title>
<link rel="stylesheet" href="https://fonts.googleapis.com/css2?family=Montserrat:wght@400;500;700;800&display=swap">
<style>
  :root {
    --bg: #b4b4b4;
    --brand-blue: #0a5ba6;
    --brand-blue-deep: #084f93;
    --brand-orange: #f2b13f;
    --paper: #ffffff;
    --ink-light: #e8eef7;
  }
  * { margin: 0; padding: 0; box-sizing: border-box; }
  html, body { width: 1200px; height: 900px; overflow: hidden; }
  body {
    background: var(--bg);
    font-family: "Montserrat", sans-serif;
    position: relative;
  }
  .card {
    position: absolute;
    left: 240px;
    width: 720px;
    height: 400px;
    background: var(--brand-blue);
    border-right: 5px solid var(--brand-orange);
    border-bottom: 5px solid var(--brand-orange);
    overflow: hidden;
    box-shadow: 0 10px 24px rgba(0,0,0,0.25);
  }
  .card--front { top: 36px; }
  .card--back { top: 470px; }

  .front-art { position: absolute; inset: 0; }

  .front-brand {
    position: absolute;
    left: 470px;
    top: 112px;
    width: 230px;
    text-align: center;
    color: var(--brand-blue);
    font-weight: 800;
    font-size: 24px;
    line-height: 1.15;
    text-transform: uppercase;
  }

  .person { position: absolute; left: 44px; top: 150px; }
  .person__name {
    color: var(--brand-orange);
    font-weight: 700;
    font-size: 30px;
  }
  .person__title {
    color: var(--ink-light);
    font-size: 15px;
    font-weight: 400;
    margin-top: 4px;
  }

  .address {
    position: absolute;
    left: 44px;
    top: 262px;
    color: var(--ink-light);
    font-size: 15px;
    line-height: 1.35;
  }
  .contacts {
    position: absolute;
    left: 44px;
    top: 316px;
    list-style: none;
    color: var(--ink-light);
    font-size: 15px;
    line-height: 1.5;
  }
  .contacts li { display: flex; align-items: center; gap: 10px; }
  .contacts svg { width: 14px; height: 14px; flex: none; }

  .back-field {
    position: absolute;
    inset: 0;
    background: linear-gradient(135deg, #0d62b0, var(--brand-blue-deep));
  }
  .back-brand {
    position: absolute;
    inset: 0;
    display: flex;
    align-items: center;
    justify-content: center;
    gap: 16px;
    color: var(--paper);
    font-weight: 800;
    font-size: 38px;
    text-transform: uppercase;
    text-align: center;
    line-height: 1.1;
  }
  .back-brand__dot {
    width: 22px; height: 22px;
    border-radius: 50%;
    background: var(--brand-orange);
    flex: none;
  }
</style>
</head>
<body>

<section class="card card--front" aria-label="Business card front">
  <svg class="front-art" viewBox="0 0 720 400" aria-hidden="true">
    <path d="M470 0 L720 0 L720 258 C650 318 520 326 478 238 C446 168 444 70 470 0 Z" fill="var(--paper)"/>
    <path d="M478 30 C440 120 446 220 486 262 C540 322 650 312 720 262" fill="none" stroke="var(--brand-orange)" stroke-width="4"/>
  </svg>
  <div class="front-brand">Frostvale<br>Harborline LLC</div>

  <div class="person">
    <div class="person__name">Dana Mercer</div>
    <div class="person__title">Managing Director</div>
  </div>

  <div class="address">48 Ridgeway Avenue,<br>Alder Falls, NY 13090</div>

  <ul class="contacts">
    <li>
      <svg viewBox="0 0 14 14"><rect x="3" y="1" width="8" height="12" rx="1.5" fill="none" stroke="var(--brand-orange)" stroke-width="1.6"/></svg>
      +1 (555) 014-2378
    </li>
    <li>
      <svg viewBox="0 0 14 14"><rect x="1" y="3" width="12" height="9" fill="var(--brand-orange)"/><path d="M1 3 L7 8 L13 3" fill="none" stroke="var(--brand-blue)" stroke-width="1.2"/></svg>
      hello@frostvaleharbor.com
    </li>
    <li>
      <svg viewBox="0 0 14 14"><circle cx="7" cy="7" r="6" fill="var(--brand-orange)"/><path d="M1 7 H13 M7 1 C4 4 4 10 7 13 M7 1 C10 4 10 10 7 13" fill="none" stroke="var(--brand-blue)" stroke-width="1"/></svg>
      www.frostvaleharbor.com
    </li>
  </ul>
</section>

<section class="card card--back" aria-label="Business card back">
  <div class="back-field" role="img" aria-label="Faint repeated brand pattern on blue background"></div>
  <div class="back-brand">
    <span class="back-brand__dot"></span>
    <span>Frostvale<br>Harborline LLC</span>
  </div>
</section>

</body>
</html>
```